Web Developer Needs a Business Card Design

I need a personal business card design that represents me as a web developer for potential employers. I would like the background to be a dark color on the front for contrast with my logo and name. The back will have all my information along with a smaller version of the logo. I want something with a modern look and feel, not too conservative. This will be used for potential employers and freelance work.

Industry/Entity Type

Business

Contact Information for Business Card

Front should have my logo and name. The back should have all my personal information which would include: name: Tom Varulek, phone: 570-614-3098, email: tomvarulek@quillbox.net, website url: www.tomvarulek.net, logo, web developer.

Font styles to use
Sans Serif

Requirements
Must have
• Must include my logo. The color palette base color will be the logo color.

```html
<!DOCTYPE html>
<html lang="en">
<head>
<meta charset="utf-8">
<title>Tom Varulek — Business Card</title>
<link rel="stylesheet" href="https://fonts.googleapis.com/css2?family=Open+Sans:wght@400;600;700&display=swap">
<style>
  :root {
    --teal: #00877a;
    --teal-dark: #00766b;
    --teal-light: #1a9588;
    --paper: #ffffff;
    --ink: #1d1d1d;
    --muted: #5a5a5a;
    --backdrop: #eceeed;
  }
  * { box-sizing: border-box; margin: 0; padding: 0; }
  html, body { width: 1200px; height: 905px; overflow: hidden; }
  body {
    background: var(--backdrop);
    font-family: "Open Sans", Arial, sans-serif;
    position: relative;
  }
  .card {
    position: absolute;
    top: 302px;
    width: 520px;
    height: 300px;
    overflow: hidden;
    box-shadow: 0 2px 8px rgba(0,0,0,0.08);
  }
  .card-back { left: 50px; background: var(--paper); }
  .card-front { left: 630px; background: var(--teal); }

  /* back side */
  .back-art { position: absolute; inset: 0; }
  .back-brand {
    position: absolute; left: 40px; top: 22px;
    display: flex; align-items: center; gap: 12px;
    color: var(--paper); font-weight: 600; font-size: 15px;
  }
  .brand-dot {
    width: 46px; height: 46px; border-radius: 50%;
    border: 4px solid var(--paper);
  }
  .identity { position: absolute; left: 40px; top: 118px; }
  .identity-name { color: var(--teal); font-weight: 700; font-size: 24px; line-height: 1.1; }
  .identity-role { color: var(--muted); font-size: 13px; margin-top: 2px; }
  .contacts {
    position: absolute; left: 285px; top: 192px;
    list-style: none; display: grid; gap: 9px;
  }
  .contact { display: flex; align-items: center; gap: 10px; color: var(--ink); font-size: 12px; font-weight: 600; }
  .contact-phone { font-size: 19px; font-weight: 700; }
  .contact-icon { width: 14px; height: 14px; flex: none; }

  /* front side */
  .front-brand {
    position: absolute; inset: 0;
    display: flex; flex-direction: column; align-items: center; justify-content: center; gap: 16px;
  }
  .front-dot {
    width: 78px; height: 78px; border-radius: 50%;
    border: 6px solid var(--paper);
  }
  .front-name { color: var(--paper); font-weight: 600; font-size: 30px; letter-spacing: 0.5px; }
</style>
</head>
<body>

<section class="card card-back" aria-label="Card back">
  <svg class="back-art" width="520" height="300" viewBox="0 0 520 300" aria-hidden="true">
    <polygon class="header-band" points="0,0 520,0 520,172 312,172 252,92 0,92" fill="var(--teal)"/>
  </svg>
  <svg class="back-art" width="520" height="300" viewBox="0 0 520 300" role="img" aria-label="Faceted low-poly teal pattern">
    <defs>
      <linearGradient id="facet" x1="0" y1="0" x2="1" y2="1">
        <stop offset="0" stop-color="var(--teal-light)"/>
        <stop offset="1" stop-color="var(--teal-dark)"/>
      </linearGradient>
    </defs>
    <polygon points="252,92 340,0 520,0 520,172 312,172" fill="url(#facet)"/>
  </svg>

  <div class="back-brand">
    <span class="brand-dot"></span>
    <span>Tom Varulek</span>
  </div>

  <div class="identity">
    <p class="identity-name">Tom Varulek</p>
    <p class="identity-role">web developer</p>
  </div>

  <ul class="contacts">
    <li class="contact contact-phone">
      <svg class="contact-icon" viewBox="0 0 16 16" aria-hidden="true"><rect x="0.5" y="0.5" width="15" height="15" rx="2" fill="none" stroke="var(--ink)"/><path d="M5 3.5c-1 1-1 3 1.5 6s4.5 3 5.5 2l-1.5-1.8-1.5.8c-1-.5-2.5-2-3-3l.8-1.5z" fill="var(--ink)"/></svg>
      <span>570-614-3098</span>
    </li>
    <li class="contact">
      <svg class="contact-icon" viewBox="0 0 16 16" aria-hidden="true"><circle cx="8" cy="8" r="7" fill="var(--ink)"/><path d="M1 8h14M8 1c-3 3-3 11 0 14M8 1c3 3 3 11 0 14" stroke="var(--paper)" fill="none"/></svg>
      <span>www.tomvarulek.net</span>
    </li>
    <li class="contact">
      <svg class="contact-icon" viewBox="0 0 16 16" aria-hidden="true"><circle cx="8" cy="8" r="7" fill="var(--ink)"/><rect x="4" y="5.5" width="8" height="5" fill="none" stroke="var(--paper)"/><path d="M4 5.5l4 3 4-3" stroke="var(--paper)" fill="none"/></svg>
      <span>tomvarulek@quillbox.net</span>
    </li>
  </ul>
</section>

<section class="card card-front" aria-label="Card front">
  <div class="front-brand">
    <span class="front-dot"></span>
    <span class="front-name">Tom Varulek</span>
  </div>
</section>

</body>
</html>
```